FinTech company looking to revamp and expand client-facing interface for our financial models

Pellworth Engines currently has a very simple website that allows clients to interact with our financial models. We are looking to completely redesign the current site and add several extra pages to provide extra functionality. We want the design to have a modern, slick feel, that will work on both a desktop or a tablet. It should be straightforward for clients to move between different pages at any time, and clear from the layout how to interact with the more advanced features. We have included screenshots of existing pages in the attached design brief, as well as sketches of the functionality required by the new pages, but can't provide a direct link to the current site.
Target Market(s)
Professional investors that will be paying to access the interface
Industry/Entity Type
Finance
Number of Pages Required
4 page
Colors
Designer to choose colors to be used in the design.
Look and feel
Each slider illustrates characteristics of the customer's brand and the style your logo design should communicate.

```html
<!DOCTYPE html>
<html lang="en">
<head>
<meta charset="utf-8">
<title>QMODEL – ETF Pairs</title>
<link rel="stylesheet" href="https://fonts.googleapis.com/css2?family=Montserrat:wght@600;700&family=Open+Sans:wght@400;600;700&family=Roboto+Condensed:wght@400&display=swap">
<style>
:root{
  --frame:#e5e5e5;
  --white:#ffffff;
  --navy:#0b3366;
  --ink:#1a1a1a;
  --teal:#00706e;
  --row-alt:#efefef;
  --panel:rgba(44,44,44,0.95);
  --panel-solid:#333333;
  --tab-black:#111111;
  --line:#e2e2e2;
  --muted:#555555;
}
*{box-sizing:border-box;margin:0;padding:0}
html,body{width:1200px;height:706px;overflow:hidden;background:var(--frame)}
.stage{position:absolute;left:0;top:0;width:1300px;height:765px;transform:scale(0.923077);transform-origin:0 0;background:var(--frame);font-family:"Open Sans",sans-serif;color:var(--ink)}
.app{position:absolute;left:15px;top:15px;width:1270px;height:735px;background:linear-gradient(#ececec 0,#efefef 160px,#f7f7f7 420px,#fafafa 100%);overflow:hidden}

/* top bar */
.topbar{position:absolute;left:0;top:0;width:1270px;height:60px;background:var(--white);box-shadow:0 6px 14px rgba(0,0,0,0.08);font-family:"Montserrat",sans-serif}
.brand{position:absolute;left:58px;top:0;line-height:60px;font-size:18px;font-weight:700;letter-spacing:0.2px}
.periods{position:absolute;left:180px;top:0;display:flex;height:60px}
.period{width:90px;height:60px;line-height:60px;text-align:center;font-size:14px;font-weight:700;border-right:1px solid var(--line)}
.period.active{background:var(--navy);color:var(--white);border-right:none}
.mainnav{position:absolute;left:755px;top:0;display:flex;height:60px}
.navitem{height:60px;display:flex;align-items:center;justify-content:center;gap:8px;font-size:13px;font-weight:700;border-right:1px solid var(--line)}
.navitem.active{background:var(--navy);color:var(--white)}
.navitem svg{width:24px;height:24px}

/* tabs */
.tab{position:absolute;background:var(--white);font-family:"Montserrat",sans-serif;font-size:13px;font-weight:600;color:#333;text-align:center;border-radius:6px 6px 0 0;box-shadow:0 -2px 6px rgba(0,0,0,0.05)}
.tab.short{top:120px;height:35px;line-height:38px}
.tab.mid{top:110px;height:45px;line-height:46px}
.tab.active{top:100px;height:55px;line-height:56px;background:var(--tab-black);color:var(--white);font-weight:700}
.tab-arrow{position:absolute;left:1175px;top:120px;width:35px;height:35px;background:var(--white);border-radius:6px 6px 0 0;display:flex;align-items:center;justify-content:center}
.tab-add{position:absolute;left:1220px;top:120px;width:40px;height:35px;background:var(--navy);border-radius:6px 6px 0 0;display:flex;align-items:center;justify-content:center}

/* export */
.export{position:absolute;left:1150px;top:197px;display:flex;align-items:center;gap:8px;color:var(--navy);font-family:"Montserrat",sans-serif;font-size:17px;font-weight:700}

/* table */
.models{position:absolute;left:90px;top:235px;width:1160px;border-radius:6px;overflow:hidden;box-shadow:0 2px 8px rgba(0,0,0,0.08);background:var(--white)}
.row{display:grid;grid-template-columns:100px 140px 115px 85px repeat(8,90px);height:70px}
.row.head{background:var(--teal);color:var(--white);font-family:"Montserrat",sans-serif;font-weight:700;font-size:16px}
.row.head .cell{justify-content:center;border-right:1px solid rgba(255,255,255,0.25)}
.row.alt{background:var(--row-alt)}
.cell{display:flex;align-items:center;padding-left:9px;border-right:1px solid var(--line);font-family:"Roboto Condensed",sans-serif;font-size:16px;line-height:20px}
.cell.label{font-size:16px;color:#222}

/* filter panel */
.filters{position:absolute;left:0;top:155px;width:445px;height:580px;background:var(--panel);color:var(--white)}
.filters h2{position:absolute;left:184px;top:84px;font-size:19px;font-weight:700;letter-spacing:0.3px}
.field{position:absolute;left:40px;display:flex;align-items:center;font-size:16px;font-weight:600}
.field .name{width:86px}
.field .thr{width:102px}
.field .input{width:181px;height:30px;background:var(--white);border-radius:5px;color:var(--ink);font-weight:400;font-size:16px;padding-left:12px;line-height:30px}
.apply{position:absolute;left:40px;top:281px;display:flex;align-items:center;font-size:16px;font-weight:600}
.check{width:17px;height:17px;background:var(--white);border-radius:3px;margin:0 9px 0 16px}
.search{position:absolute;left:145px;top:355px;width:155px;height:50px;background:var(--navy);border:2px solid var(--white);border-radius:6px;font-size:15px;font-weight:700;display:flex;align-items:center;justify-content:center}
.close-tab{position:absolute;left:445px;top:320px;width:50px;height:250px;background:var(--panel-solid);border-radius:0 6px 6px 0;color:var(--white)}
.close-tab span{position:absolute;left:25px;top:125px;transform:translate(-50%,-50%) rotate(-90deg);white-space:nowrap;font-size:15px;font-weight:700;letter-spacing:0.8px}
.close-btn{position:absolute;left:482px;top:432px;width:26px;height:26px}
</style>
</head>
<body>
<div class="stage">
  <div class="app">
    <header class="topbar">
      <div class="brand">QMODEL</div>
      <nav class="periods">
        <div class="period active">250D</div>
        <div class="period">83D</div>
        <div class="period">42D</div>
      </nav>
      <nav class="mainnav">
        <div class="navitem active" style="width:140px">
          <svg viewBox="0 0 24 24" fill="none" stroke="#fff" stroke-width="2"><path d="M3 11 12 3l9 8"/><path d="M5 10v10h5v-6h4v6h5V10"/></svg>MODELS</div>
        <div class="navitem" style="width:178px">
          <svg viewBox="0 0 24 24" fill="#222"><circle cx="12" cy="12" r="3"/><g><circle cx="12" cy="3" r="1.4"/><circle cx="12" cy="21" r="1.4"/><circle cx="3" cy="12" r="1.4"/><circle cx="21" cy="12" r="1.4"/><circle cx="5.6" cy="5.6" r="1.4"/><circle cx="18.4" cy="18.4" r="1.4"/><circle cx="18.4" cy="5.6" r="1.4"/><circle cx="5.6" cy="18.4" r="1.4"/><circle cx="12" cy="7" r="1"/><circle cx="12" cy="17" r="1"/><circle cx="7" cy="12" r="1"/><circle cx="17" cy="12" r="1"/></g></svg>SENSITIVITIES</div>
        <div class="navitem" style="width:197px;border-right:none">
          <svg viewBox="0 0 24 24" fill="none" stroke="#222" stroke-width="1.8"><path d="M12 2.5l2.9 6.1 6.6.8-4.9 4.6 1.3 6.6L12 17.3l-5.9 3.3 1.3-6.6-4.9-4.6 6.6-.8z"/></svg>FAVOURITES</div>
      </nav>
    </header>

    <div class="tab short" style="left:55px;width:155px">EQUITIES</div>
    <div class="tab short" style="left:215px;width:155px">ETFS</div>
    <div class="tab mid" style="left:375px;width:155px">PAIRS</div>
    <div class="tab active" style="left:535px;width:155px">ETF PAIRS</div>
    <div class="tab mid" style="left:695px;width:155px">FACTORS</div>
    <div class="tab short" style="left:855px;width:155px">NEW TAB TITLE #1</div>
    <div class="tab short" style="left:1015px;width:155px">NEW TAB TITLE #2</div>
    <div class="tab-arrow"><svg width="16" height="20" viewBox="0 0 16 20"><path d="M4 2l8 8-8 8" fill="none" stroke="#999" stroke-width="3"/></svg></div>
    <div class="tab-add"><svg width="26" height="26" viewBox="0 0 26 26" fill="none" stroke="#fff" stroke-width="2"><circle cx="13" cy="13" r="11"/><path d="M13 7v12M7 13h12"/></svg></div>

    <div class="export"><svg width="26" height="24" viewBox="0 0 26 24" fill="none" stroke="#0b3366" stroke-width="2.2"><path d="M11 5H4v16h16v-7"/><path d="M10 16c1-6 5-9 12-9"/><path d="M17 3l5 4-5 4"/></svg>Export</div>

    <div class="models">
      <div class="row head">
        <div class="cell">ID ⌄</div><div class="cell">Sector</div><div class="cell">Time</div><div class="cell">Quality</div>
        <div class="cell">Stat 1</div><div class="cell">Stat 2</div><div class="cell">Stat 3</div><div class="cell">Stat 4</div><div class="cell">Stat 5</div><div class="cell">Stat 6</div><div class="cell">Stat 7</div><div class="cell">Stat 8</div>
      </div>
      <div class="row">
        <div class="cell label">Model 1</div><div class="cell label">Materials</div><div class="cell label">2019-07-03<br>12:15:00.000</div><div class="cell">30.2288</div>
        <div class="cell">2.01574</div><div class="cell">23.305</div><div class="cell">-0.149368</div><div class="cell">22.3054</div><div class="cell">4.63714</div><div class="cell">0.945706</div><div class="cell">2.81949</div><div class="cell">2.60858</div>
      </div>
      <div class="row alt">
        <div class="cell label">Model 2</div><div class="cell label">Industrials</div><div class="cell label">2019-07-03<br>12:15:00.000</div><div class="cell">42.8694</div>
        <div class="cell">0.87307</div><div class="cell">32.185</div><div class="cell">-0.033692</div><div class="cell">33.9911</div><div class="cell">11.5693</div><div class="cell">-0.472968</div><div class="cell">-0.830458</div><div class="cell">6.80646</div>
      </div>
      <div class="row">
        <div class="cell label">Model 3</div><div class="cell label">Consumer<br>Discretionary</div><div class="cell label">2019-07-03<br>12:15:00.000</div><div class="cell">56.6002</div>
        <div class="cell">-0.569222</div><div class="cell">159.814</div><div class="cell">0.0252328</div><div class="cell">172.616</div><div class="cell">10.2875</div><div class="cell">-0.750396</div><div class="cell">-0.385309</div><div class="cell">4.69146</div>
      </div>
      <div class="row alt">
        <div class="cell label">Model 4</div><div class="cell label">Information<br>Technology</div><div class="cell label">2019-07-03<br>12:15:00.000</div><div class="cell">45.6856</div>
        <div class="cell">0.412148</div><div class="cell">202.488</div><div class="cell">0.0084923</div><div class="cell">205.834</div><div class="cell">11.9094</div><div class="cell">-0.137913</div><div class="cell">0.449595</div><div class="cell">3.85106</div>
      </div>
      <div class="row">
        <div class="cell label">Model 5</div><div class="cell label">Information<br>Technology</div><div class="cell label">2019-07-03<br>12:15:00.000</div><div class="cell">75.7733</div>
        <div class="cell">7.06728</div><div class="cell">188.605</div><div class="cell">0.016913</div><div class="cell">161.665</div><div class="cell">3.82241</div><div class="cell">0.981019</div><div class="cell">1.29847</div><div class="cell">3.34927</div>
      </div>
    </div>

    <aside class="filters">
      <h2>FILTERS</h2>
      <div class="field" style="top:170px"><span class="name">Quality</span><span class="thr">Threshold:</span><span class="input">-10</span></div>
      <div class="field" style="top:230px"><span class="name">Abs. Stat</span><span class="thr">Threshold:</span><span class="input">-10</span></div>
      <div class="apply">Apply Filter<span class="check"></span>All tabs<span class="check" style="margin-left:18px"></span>Current tab</div>
      <div class="search">SEARCH</div>
    </aside>
    <div class="close-tab"><span>CLOSE FILTERS</span></div>
    <svg class="close-btn" viewBox="0 0 26 26"><circle cx="13" cy="13" r="12" fill="#0b3366" stroke="#fff" stroke-width="2"/><path d="M18 13H8M12 9l-4 4 4 4" fill="none" stroke="#fff" stroke-width="2"/></svg>
  </div>
</div>
</body>
</html>
```